Website update for Harborline Ledger Partners & Bookkeeping

Our website needs updating
www.harborlineledgerpartners.com
Here are some of our latest print pieces to use as a guide?
I have also attached our graphic identity guide which includes the Pantone colors

Target Market(s)

Insurance Agencies

Industry/Entity Type

Accounting

Number of Pages Required

5+ page

```html
<!DOCTYPE html>
<html lang="en">
<head>
<meta charset="utf-8">
<title>Harborline Ledger Partners &amp; Bookkeeping</title>
<link href="https://fonts.googleapis.com/css2?family=Open+Sans:wght@300;400;600;700&display=swap" rel="stylesheet">
<style>
:root{
  --teal:#16a394;
  --teal-dark:#0f8a7d;
  --ink:#3b3f44;
  --muted:#8a9096;
  --line:#e3e6e8;
  --paper:#ffffff;
  --mist:#f3f4f5;
}
*{box-sizing:border-box;margin:0;padding:0}
html,body{width:1200px;height:2248px;overflow:hidden}
body{font-family:"Open Sans",Arial,sans-serif;color:var(--ink);background:var(--paper);position:relative}
.topbar{height:40px;background:var(--mist);display:flex;align-items:center;justify-content:space-between;padding:0 60px 0 60px;font-size:12px;color:var(--muted)}
.topbar .right{display:flex;align-items:center;gap:18px}
.social{width:14px;height:14px;border-radius:50%;background:#a6acb1}
.contact-btn{background:var(--teal);color:#fff;height:40px;line-height:40px;padding:0 22px;font-size:12px;font-weight:600}
.header{height:110px;position:relative;padding:0 60px;display:flex;align-items:center;justify-content:space-between}
.brand{display:flex;align-items:center;gap:14px}
.brand .mark{width:38px;height:38px;background:var(--teal)}
.brand .name{font-weight:700;font-size:18px;color:var(--teal);line-height:1.2;width:250px}
.phone{display:flex;align-items:center;gap:10px;font-size:26px;font-weight:600;color:var(--teal);margin-top:-26px}
.nav{position:absolute;left:440px;right:60px;bottom:0;height:30px;background:var(--teal);display:flex;align-items:center;gap:34px;padding:0 24px;font-size:11px;font-weight:600;color:#fff;letter-spacing:.5px}
.hero{position:relative;height:510px;overflow:hidden}
.hero .photo{position:absolute;inset:0;background:linear-gradient(100deg,#9aa0a4 0%,#c7cbcd 40%,#e6e7e6 70%,#d8d9d8 100%)}
.hero .copy{position:absolute;left:160px;top:120px;color:#fff}
.hero h1{font-weight:300;font-size:56px;line-height:1.15;letter-spacing:1px}
.hero h1 b{font-weight:700}
.hero p{margin-top:30px;font-size:20px;line-height:1.4;width:380px}
.hero .ribbon{position:absolute;right:0;bottom:0;width:720px;height:70px;background:var(--teal);clip-path:polygon(10% 0,100% 0,100% 100%,0 100%)}
.needs{display:flex;height:170px}
.needs .ask{width:480px;padding:50px 40px 0 150px;text-align:right}
.needs .ask small{font-size:15px;font-weight:600;display:block}
.needs .ask strong{font-size:24px;font-weight:600;color:var(--teal);line-height:1.3}
.needs ul{flex:1;background:var(--teal);color:#fff;list-style:none;padding:28px 60px 0 50px;font-size:12px;line-height:1.45}
.needs li{position:relative;padding-left:18px;margin-bottom:10px}
.needs li:before{content:"";position:absolute;left:0;top:5px;width:7px;height:7px;background:#fff;border-radius:50%}
.section-title{text-align:center;font-size:34px;font-weight:300}
.section-title b{font-weight:600;color:var(--teal)}
.services{padding-top:50px;height:400px}
.services .lead{text-align:center;font-size:15px;color:var(--muted);width:720px;margin:14px auto 0;line-height:1.5}
.cards{display:flex;justify-content:center;gap:40px;margin-top:34px}
.card{width:220px;border:1px solid var(--line)}
.card .icon{height:100px;background:linear-gradient(#f6f7f7,#eceeee)}
.card .label{padding:14px 20px;text-align:center;color:var(--teal);font-weight:600;font-size:13px;line-height:1.35}
.how{display:flex;padding:0 60px 0 160px;height:350px;gap:60px}
.how .intro{width:300px;padding-top:30px}
.how h2{font-size:34px;font-weight:300}
.how h2 b{font-weight:600;color:var(--teal)}
.how .intro p{font-size:12px;color:var(--muted);line-height:1.6;margin:16px 0 22px}
.btn{display:inline-block;background:var(--teal);color:#fff;font-size:11px;font-weight:600;padding:9px 18px}
.features{flex:1;display:grid;grid-template-columns:1fr 1fr;gap:30px 40px;padding-top:40px}
.feature{display:flex;gap:14px}
.feature svg{flex:none}
.feature h3{font-size:13px;font-weight:600;margin-bottom:6px}
.feature p{font-size:11px;color:var(--muted);line-height:1.5}
.team{height:400px;padding-top:40px;text-align:center}
.faces{display:flex;justify-content:center;align-items:center;gap:60px;margin-top:30px}
.face{border-radius:50%;background:linear-gradient(#c9cdd0,#aeb3b7)}
.team .who{font-size:12px;font-weight:600;color:var(--teal);margin-top:8px}
.team .bio{width:800px;margin:16px auto 0;font-size:12px;color:var(--muted);line-height:1.6}
.dots{display:flex;justify-content:center;gap:8px;margin-top:18px}
.dots i{width:8px;height:8px;border-radius:50%;background:#c6cbce}
.dots i:first-child{background:var(--teal)}
.footer{position:absolute;left:0;top:2000px;width:1200px;height:224px;background:var(--teal);color:#fff;display:flex;padding:50px 60px 0 160px}
.cols{display:flex;gap:50px;flex:1}
.col{width:110px;text-align:center;font-size:11px;line-height:1.5}
.col svg{display:block;margin:0 auto 8px}
.col b{display:block;font-size:13px;margin-bottom:4px}
.newsletter{width:300px;background:var(--teal-dark);padding:22px}
.newsletter h4{font-size:14px;font-weight:600;margin-bottom:14px}
.newsletter .field{height:32px;background:#fff;margin-bottom:10px}
.newsletter .btn{background:#0a6e64}
.copyright{position:absolute;left:0;top:2224px;width:1200px;height:24px;background:#0c7c70;color:#d6f0ed;font-size:10px;text-align:center;line-height:24px}
</style>
</head>
<body>
<div class="topbar">
  <span>info@harborlineledgerpartners.com</span>
  <div class="right"><span class="social"></span><span class="social"></span><span class="social"></span><span class="contact-btn">Contact Us</span></div>
</div>
<header class="header">
  <div class="brand"><span class="mark"></span><span class="name">Harborline Ledger Partners &amp; Bookkeeping</span></div>
  <div class="phone"><svg width="24" height="24" viewBox="0 0 24 24"><path fill="#16a394" d="M6.6 10.8a15 15 0 0 0 6.6 6.6l2.2-2.2a1 1 0 0 1 1-.25 11 11 0 0 0 3.6.6 1 1 0 0 1 1 1V20a1 1 0 0 1-1 1A17 17 0 0 1 3 4a1 1 0 0 1 1-1h3.5a1 1 0 0 1 1 1 11 11 0 0 0 .6 3.6 1 1 0 0 1-.25 1z"/></svg>860-555-0142</div>
  <nav class="nav"><span>HOME</span><span>ABOUT US</span><span>CAREERS</span><span>OUR SERVICES</span><span>HOW IT WORKS</span><span>RESOURCES</span><span>BLOG</span></nav>
</header>
<section class="hero">
  <div class="photo" role="img" aria-label="Photo of a professional woman working on a laptop at a bright desk"></div>
  <div class="copy">
    <h1>LEARN<br>WHY <b>HLP</b> IS THE</h1>
    <p>Leading remote bookkeeping firm for Ledgerly and Policyware agencies.</p>
  </div>
  <div class="ribbon"></div>
</section>
<section class="needs">
  <div class="ask"><small>Need help with your insurance</small><strong>Agency's accounting and bookkeeping?</strong></div>
  <ul>
    <li>First and only firm of insurance agency bookkeeping professionals focused on your books.</li>
    <li>Ours is a fully trained team working in a secure office with clear separation of duties and review.</li>
    <li>All accounts handled remotely, reconciled monthly and reported on time by staff with real agency experience.</li>
  </ul>
</section>
<section class="services">
  <h2 class="section-title">Services <b>Available</b></h2>
  <p class="lead">After working in house at agencies for many years, Marissa Colton formed HLP in 2011 to help independent insurance agencies manage their accounting and bookkeeping.</p>
  <div class="cards">
    <div class="card"><div class="icon" role="img" aria-label="Illustration of a piggy bank"></div><div class="label">Record Direct<br>Bill Commission</div></div>
    <div class="card"><div class="icon" role="img" aria-label="Illustration of banknotes"></div><div class="label">Reconcile &amp; Pay Agency<br>Bill Premiums</div></div>
    <div class="card"><div class="icon" role="img" aria-label="Illustration of a ledger document"></div><div class="label">Reconcile General<br>Ledger Accounts</div></div>
  </div>
</section>
<section class="how">
  <div class="intro">
    <h2>How <b>It Works</b></h2>
    <p>HLP has the capability to perform all your bookkeeping functions so in house staff can focus on clients. Our trained team works remotely, delivers reports on schedule and keeps every account reconciled and reviewed.</p>
    <span class="btn">VIEW ALL</span>
  </div>
  <div class="features">
    <div class="feature"><svg width="40" height="40" viewBox="0 0 40 40"><circle cx="20" cy="20" r="19" fill="#16a394"/><circle cx="20" cy="15" r="5" fill="#fff"/><path d="M11 30a9 7 0 0 1 18 0z" fill="#fff"/></svg><div><h3>Educated &amp; Trained Staff</h3><p>Our team holds degrees and years of agency accounting experience.</p></div></div>
    <div class="feature"><svg width="40" height="40" viewBox="0 0 40 40"><circle cx="20" cy="20" r="19" fill="#16a394"/><path d="M12 20l6 6 11-12" stroke="#fff" stroke-width="3" fill="none"/></svg><div><h3>Quality Control</h3><p>Every reconciliation is reviewed by a second accountant each month.</p></div></div>
    <div class="feature"><svg width="40" height="40" viewBox="0 0 40 40"><circle cx="20" cy="20" r="19" fill="#16a394"/><path d="M12 14h16M12 20h16M12 26h16" stroke="#fff" stroke-width="3"/></svg><div><h3>Separation of Duties</h3><p>Clear split of tasks protects the agency and keeps records clean.</p></div></div>
    <div class="feature"><svg width="40" height="40" viewBox="0 0 40 40"><circle cx="20" cy="20" r="19" fill="#16a394"/><path d="M20 9l9 4v7c0 6-4 10-9 12-5-2-9-6-9-12v-7z" fill="#fff"/></svg><div><h3>Data Security</h3><p>Encrypted systems and secure offices guard all client data.</p></div></div>
  </div>
</section>
<section class="team">
  <h2 class="section-title">Our <b>Experienced Team</b></h2>
  <div class="faces">
    <div class="face" style="width:60px;height:60px" role="img" aria-label="Team member portrait"></div>
    <div class="face" style="width:120px;height:120px" role="img" aria-label="Portrait of Marissa Colton"></div>
    <div class="face" style="width:60px;height:60px" role="img" aria-label="Team member portrait"></div>
  </div>
  <div class="who">Marissa Colton<br><span style="font-weight:400;color:#8a9096">Founder</span></div>
  <p class="bio">Marissa spent many years working in house at independent agencies before founding HLP. She leads a team that handles commission, premium and ledger work for agencies across the country, bringing the same care to every client file and every monthly close.</p>
  <div class="dots"><i></i><i></i><i></i></div>
</section>
<footer class="footer">
  <div class="cols">
    <div class="col"><svg width="30" height="30" viewBox="0 0 24 24"><path fill="#fff" d="M12 2a7 7 0 0 0-7 7c0 5 7 13 7 13s7-8 7-13a7 7 0 0 0-7-7zm0 9.5A2.5 2.5 0 1 1 12 6.5a2.5 2.5 0 0 1 0 5z"/></svg><b>Address</b>142 Quay Road Suite 4<br>Mystic, CT 06355</div>
    <div class="col"><svg width="30" height="30" viewBox="0 0 24 24"><path fill="#fff" d="M6.6 10.8a15 15 0 0 0 6.6 6.6l2.2-2.2a1 1 0 0 1 1-.25 11 11 0 0 0 3.6.6 1 1 0 0 1 1 1V20a1 1 0 0 1-1 1A17 17 0 0 1 3 4a1 1 0 0 1 1-1h3.5a1 1 0 0 1 1 1 11 11 0 0 0 .6 3.6 1 1 0 0 1-.25 1z"/></svg><b>Phone</b>860-555-0142</div>
    <div class="col"><svg width="30" height="30" viewBox="0 0 24 24"><path fill="#fff" d="M6 3h9v5H6zM4 9h16v8h-3v4H7v-4H4zm5 6v4h6v-4z"/></svg><b>Fax</b>860-555-0143</div>
    <div class="col"><svg width="30" height="30" viewBox="0 0 24 24"><path fill="#fff" d="M3 5h18v14H3zm2 2v.5l7 5 7-5V7l-7 5z"/></svg><b>Email</b>info@harborline<br>ledgerpartners.com</div>
  </div>
  <div class="newsletter"><h4>Subscribe to our Newsletter</h4><div class="field"></div><span class="btn">SUBSCRIBE</span></div>
</footer>
<div class="copyright">© 2024 Harborline Ledger Partners &amp; Bookkeeping. All Rights Reserved.</div>
</body>
</html>
```